Business Card Design

I already have a company logo for my company. I have a logo for the manufacturer we represent. I want a professional business card design.

```html
<!DOCTYPE html>
<html lang="en">
<head>
<meta charset="utf-8">
<title>Beacon Alert Systems – Business Card</title>
<link rel="stylesheet" href="https://fonts.googleapis.com/css2?family=Open+Sans:wght@400;600;700&display=swap">
<style>
  :root{
    --stage:#232323;
    --card:#1e1e21;
    --red:#e41e2a;
    --gold:#c8962a;
    --white:#f4f4f4;
    --silver:#c4c4c6;
  }
  *{margin:0;padding:0;box-sizing:border-box}
  html,body{width:1200px;height:780px;overflow:hidden;background:var(--stage)}
  body{font-family:"Open Sans",Arial,sans-serif;position:relative}
  .card{position:absolute;top:240px;width:525px;height:300px;border-radius:18px;background:var(--card);overflow:hidden;box-shadow:0 10px 30px rgba(0,0,0,.45)}
  .card--front{left:45px}
  .card--back{left:630px}
  .card__wave{position:absolute;inset:0;width:525px;height:300px}
  .brand{position:absolute;display:flex;align-items:center;gap:8px;font-weight:700;text-transform:uppercase;letter-spacing:.04em}
  .brand__dot{width:14px;height:14px;border-radius:50%;background:var(--red);flex:none}
  .card--front .brand{left:34px;top:58px;font-size:15px;color:var(--white);line-height:1.1;width:200px}
  .divider{position:absolute;left:250px;top:62px;width:1.5px;height:124px;background:var(--gold)}
  .contact{position:absolute;left:272px;top:72px;color:var(--white)}
  .contact__name{font-size:27px;font-weight:700;line-height:1.05;white-space:nowrap}
  .contact__first{color:var(--red)}
  .contact__last{color:var(--gold)}
  .contact__title{font-size:15px;font-weight:600;margin-top:2px}
  .contact__list{list-style:none;margin-top:14px;font-size:13.5px;line-height:1.65}
  .contact__list li{display:flex;align-items:center;gap:8px}
  .contact__list svg{width:12px;height:12px;flex:none}
  .address{position:absolute;left:30px;bottom:12px;font-size:12.5px;color:var(--white);letter-spacing:.01em}
  .card--back .brand{left:0;right:0;top:0;bottom:0;justify-content:center;font-size:28px;color:var(--silver);gap:14px}
  .card--back .brand__dot{width:22px;height:22px;background:var(--silver)}
</style>
</head>
<body>
  <section class="card card--front" aria-label="Business card front">
    <svg class="card__wave" viewBox="0 0 525 300" aria-hidden="true">
      <path d="M0,128 C100,108 160,168 220,222 C270,266 380,262 525,252 L525,300 L0,300 Z" fill="var(--gold)"/>
      <path d="M0,136 C96,120 152,176 212,232 C262,276 380,272 525,264 L525,300 L0,300 Z" fill="#111"/>
      <path d="M0,140 C92,126 148,180 208,236 C258,280 380,276 525,268 L525,300 L0,300 Z" fill="var(--red)"/>
    </svg>
    <div class="brand"><span class="brand__dot"></span>Beacon Alert Systems</div>
    <div class="divider"></div>
    <div class="contact">
      <p class="contact__name"><span class="contact__first">Daniel</span> <span class="contact__last">Reyes</span></p>
      <p class="contact__title">Managing Director</p>
      <ul class="contact__list">
        <li><svg viewBox="0 0 12 12"><path d="M2.5 1 4.5 1 5.2 3.5 4 4.6C4.7 6 6 7.3 7.4 8L8.5 6.8 11 7.5 11 9.5C11 10.3 10.3 11 9.5 11 5 11 1 7 1 2.5 1 1.7 1.7 1 2.5 1Z" fill="var(--red)"/></svg>(555) 214-0387</li>
        <li><svg viewBox="0 0 12 12"><rect x="1" y="2.5" width="10" height="7" rx="1" fill="var(--red)"/><path d="M1.5 3 6 6.5 10.5 3" stroke="var(--card)" stroke-width="1" fill="none"/></svg>hello@beaconalert.com</li>
        <li><svg viewBox="0 0 12 12"><circle cx="6" cy="6" r="5" fill="var(--red)"/><path d="M1 6H11M6 1C4 3 4 9 6 11M6 1C8 3 8 9 6 11" stroke="var(--card)" stroke-width=".8" fill="none"/></svg>www.beaconalert.com</li>
      </ul>
    </div>
    <p class="address">1840 Oakridge Ave. Suite 310 Riverton, TX 75010</p>
  </section>

  <section class="card card--back" aria-label="Business card back">
    <div class="brand"><span class="brand__dot"></span>Beacon Alert Systems</div>
  </section>
</body>
</html>
```